Road Construction Company needs business cards

We would like a new business card designed for our business.

We're a road construction company based in Qld, Australia.

Can the business card please have the following information on it.

Name: Warren Halbeck
Position: General Manager
Phone: 0472 915 348
Email: Warren.halbeck@tovrin.com.au
Address: 87 Marrow Ave, Pendlebay, QLD, 4023
Website: www.tovrin.com.au

Visually we'd like the card to be professional and simple.

Attached is our logo.

Our website is www.tovrin.com.au

Target Market(s)

Men aged 25-60

Contact Information for Business Card

As listed in project description

Font styles to use
Serif

Requirements
Must have
• Large logo on back of card

```html
<!DOCTYPE html>
<html lang="en">
<head>
<meta charset="utf-8">
<title>Tovrin Road Construction – Business Card</title>
<link rel="stylesheet" href="https://fonts.googleapis.com/css2?family=Open+Sans:wght@400;600;700;800&display=swap">
<style>
  :root {
    --stage: #232323;
    --card-dark: #1f1f23;
    --brand-blue: #1255a6;
    --sky-blue: #45a8dc;
    --white: #ffffff;
  }
  * { box-sizing: border-box; margin: 0; padding: 0; }
  html, body {
    width: 1200px; height: 780px; overflow: hidden;
    background: var(--stage);
    font-family: "Open Sans", Arial, sans-serif;
  }
  .stage { position: relative; width: 1200px; height: 780px; }

  .card {
    position: absolute;
    width: 520px; height: 320px;
    border-radius: 22px;
    overflow: hidden;
    box-shadow: 0 14px 30px rgba(0,0,0,0.55);
  }

  /* Front: brand side */
  .card--front {
    left: 60px; top: 50px;
    background: var(--brand-blue);
    display: flex; align-items: center; justify-content: center;
  }
  .brand-name {
    color: var(--white);
    font-weight: 800;
    text-align: center;
    line-height: 1;
    text-transform: uppercase;
  }
  .card--front .brand-name__main { display: block; font-size: 64px; letter-spacing: 2px; }
  .card--front .brand-name__sub {
    display: block; font-size: 15px; letter-spacing: 9px; margin-top: 10px;
    color: var(--sky-blue); margin-right: -9px;
  }

  /* Back: contact side */
  .card--back {
    left: 620px; top: 420px;
    background: var(--card-dark);
  }
  .card__waves { position: absolute; inset: 0; width: 100%; height: 100%; }

  .card--back .brand-name {
    position: absolute; right: 30px; top: 20px;
    color: var(--brand-blue);
    text-align: right;
  }
  .card--back .brand-name__main { display: block; font-size: 40px; letter-spacing: 1px; }
  .card--back .brand-name__sub {
    display: block; font-size: 10px; letter-spacing: 5px; margin-top: 6px;
    color: var(--sky-blue); margin-right: -5px;
  }

  .contact {
    position: absolute; left: 40px; top: 166px;
    color: var(--white);
  }
  .contact__name { font-size: 21px; font-weight: 700; text-transform: uppercase; letter-spacing: 0.5px; line-height: 1.1; }
  .contact__role { font-size: 14px; line-height: 1.2; margin-top: 1px; }
  .contact__address { font-size: 13px; line-height: 1.25; margin-top: 8px; font-style: normal; }
  .contact__list { list-style: none; margin-top: 8px; }
  .contact__item { display: flex; align-items: center; gap: 8px; font-size: 13px; line-height: 1.4; }
  .contact__icon { width: 13px; height: 13px; flex: none; }
</style>
</head>
<body>
<main class="stage">

  <section class="card card--front" aria-label="Card front">
    <h1 class="brand-name">
      <span class="brand-name__main">Tovrin</span>
      <span class="brand-name__sub">Road Construction</span>
    </h1>
  </section>

  <section class="card card--back" aria-label="Card back">
    <svg class="card__waves" viewBox="0 0 520 320" preserveAspectRatio="none" aria-hidden="true">
      <path d="M0,122 C160,96 360,124 520,92 L520,320 L0,320 Z" fill="var(--brand-blue)"/>
      <path d="M0,132 C160,106 360,132 520,102 L520,320 L0,320 Z" fill="var(--sky-blue)"/>
      <path d="M0,144 C160,116 360,140 520,112" fill="none" stroke="var(--card-dark)" stroke-width="4"/>
      <path d="M0,152 C160,126 360,148 520,120 L520,320 L0,320 Z" fill="var(--brand-blue)"/>
    </svg>

    <div class="brand-name">
      <span class="brand-name__main">TOVRIN</span>
      <span class="brand-name__sub">ROAD CONSTRUCTION</span>
    </div>

    <div class="contact">
      <p class="contact__name">Warren Halbeck</p>
      <p class="contact__role">General Manager</p>
      <address class="contact__address">87 Marrow Ave,<br>Pendlebay, QLD, 4023</address>
      <ul class="contact__list">
        <li class="contact__item">
          <svg class="contact__icon" viewBox="0 0 16 16" aria-hidden="true"><path fill="var(--white)" d="M3.6 1.2l2.3 2.6-1.3 1.9c.8 1.9 2.3 3.4 4.1 4.2l1.9-1.3 2.6 2.3-1.3 2.3C7 13.6 2.4 9 1.3 2.5z"/></svg>
          <span>0472 915 348</span>
        </li>
        <li class="contact__item">
          <svg class="contact__icon" viewBox="0 0 16 16" aria-hidden="true"><circle cx="8" cy="8" r="6.5" fill="none" stroke="var(--white)" stroke-width="1.4"/><path d="M1.5 8h13M8 1.5c-2.5 3-2.5 10 0 13M8 1.5c2.5 3 2.5 10 0 13" fill="none" stroke="var(--white)" stroke-width="1.2"/></svg>
          <span>www.tovrin.com.au</span>
        </li>
        <li class="contact__item">
          <svg class="contact__icon" viewBox="0 0 16 16" aria-hidden="true"><rect x="1" y="3.5" width="14" height="9.5" rx="1" fill="none" stroke="var(--white)" stroke-width="1.4"/><path d="M1.5 4l6.5 5 6.5-5" fill="none" stroke="var(--white)" stroke-width="1.4"/></svg>
          <span>Warren.halbeck@tovrin.com.au</span>
        </li>
      </ul>
    </div>
  </section>

</main>
</body>
</html>
```